Kestrel Facilities Business Card Design

We would now like to design business cards with the new Kestrel Facilities logo

Target Market(s)

Professional

Industry/Entity Type

Professional services

Contact Information for Business Card

Employee name, title, phone number, email address, corporate office address and logo.

Font styles to use
Sans Serif

Colors
0054AA
0677BA
7BADD7
CADEEF
E8F1F8

Requirements
Must have
• My logo
Should not have
• any other pictures or images besides my logo

```html
<!DOCTYPE html>
<html lang="en">
<head>
<meta charset="utf-8">
<title>Kestrel Facilities Business Card</title>
<link href="https://fonts.googleapis.com/css2?family=Montserrat:wght@400;700&display=swap" rel="stylesheet">
<style>
  :root {
    --stage: #2b2b2d;
    --brand-blue: #3276bd;
    --accent-blue: #2f6fb8;
    --stripe-grey: #a09fa2;
    --paper: #ffffff;
    --mark-silver: #d6dae3;
  }
  html, body {
    margin: 0;
    padding: 0;
    width: 1200px;
    height: 960px;
    overflow: hidden;
    background: var(--stage);
    font-family: "Montserrat", Arial, sans-serif;
  }
  .canvas {
    position: relative;
    width: 1200px;
    height: 960px;
  }
  .card {
    position: absolute;
    left: 250px;
    width: 700px;
    height: 400px;
    border-radius: 22px;
    overflow: hidden;
    box-shadow: 0 14px 30px rgba(0,0,0,0.45);
  }
  .card-back {
    top: 50px;
    background: var(--brand-blue);
    display: flex;
    align-items: center;
    justify-content: center;
  }
  .card-front {
    top: 500px;
    background: var(--paper);
  }
  .card-front .wave {
    position: absolute;
    inset: 0;
    width: 700px;
    height: 400px;
  }
  .brand {
    display: flex;
    align-items: center;
    gap: 14px;
    font-weight: 700;
    letter-spacing: 1px;
  }
  .brand-square {
    display: block;
    border: 6px solid currentColor;
  }
  .card-back .brand {
    color: var(--mark-silver);
    font-size: 40px;
  }
  .card-back .brand-square { width: 42px; height: 42px; }
  .card-front .brand {
    position: absolute;
    top: 36px;
    right: 50px;
    color: var(--brand-blue);
    font-size: 28px;
  }
  .card-front .brand-square { width: 28px; height: 28px; border-width: 5px; }
  .contact {
    position: absolute;
    left: 58px;
    bottom: 26px;
    color: var(--paper);
  }
  .person-name {
    margin: 0;
    font-size: 24px;
    font-weight: 700;
    letter-spacing: 0.5px;
    line-height: 1.2;
  }
  .person-title {
    margin: 2px 0 12px;
    font-size: 17px;
    font-weight: 400;
  }
  .address {
    margin: 0 0 10px;
    font-size: 15px;
    line-height: 1.35;
    font-style: normal;
  }
  .contact-line {
    display: flex;
    align-items: center;
    gap: 8px;
    margin: 0;
    font-size: 15px;
    line-height: 1.45;
  }
  .contact-line svg { width: 16px; height: 16px; fill: var(--paper); }
</style>
</head>
<body>
<main class="canvas">
  <section class="card card-back" aria-label="Card back">
    <div class="brand"><span class="brand-square"></span>Kestrel Facilities</div>
  </section>

  <section class="card card-front" aria-label="Card front">
    <svg class="wave" viewBox="0 0 700 400" aria-hidden="true">
      <path d="M0,200 C150,150 330,140 480,150 C580,158 650,140 700,110 L700,400 L0,400 Z" fill="var(--brand-blue)"/>
      <path d="M20,182 C170,132 330,124 480,136 C580,144 650,128 700,98 L700,106 C650,134 580,150 480,143 C330,132 160,140 20,185 Z" fill="var(--stripe-grey)"/>
      <path d="M330,112 C470,128 590,115 690,72 L700,64 L700,78 C610,125 480,135 330,112 Z" fill="var(--accent-blue)"/>
    </svg>
    <div class="brand"><span class="brand-square"></span>Kestrel Facilities</div>
    <div class="contact">
      <h1 class="person-name">DARA WELLINGTON</h1>
      <p class="person-title">Co-Founder</p>
      <address class="address">4180 N. Harbor Lane<br>Suite 210 Easton.14</address>
      <p class="contact-line">
        <svg viewBox="0 0 24 24"><path d="M6.6 10.8a15 15 0 0 0 6.6 6.6l2.2-2.2a1 1 0 0 1 1-.25 11.4 11.4 0 0 0 3.6.57 1 1 0 0 1 1 1V20a1 1 0 0 1-1 1A17 17 0 0 1 3 4a1 1 0 0 1 1-1h3.5a1 1 0 0 1 1 1c0 1.25.2 2.45.57 3.57a1 1 0 0 1-.25 1z"/></svg>
        +254-700-41592
      </p>
      <p class="contact-line">
        <svg viewBox="0 0 24 24"><path d="M2 5h20v14H2z M2 5l10 8 10-8" fill="none" stroke="#fff" stroke-width="2"/></svg>
        hello@kestrelfacilities.com
      </p>
    </div>
  </section>
</main>
</body>
</html>
```